Velmora Consulting Business

** Please add the content information from my old business card
1. I would like to see a two sided business card with both options with the 1st Option--Tallow Spire-new WHITE BACKGROUND LOGO
2 nd Option-Tallow Spire - new BLACK- Background Logo
3rd -Option a business card with my Photo on the card
Please add the new word to the card information:
EXECUTION
AS THE OWNER'S REP
WE AIM TO ACHIEVE YOUR
INFRASTRUCTURE VISION with
OUR SPECIALIZATION & EXECUTION in:

FUNDING Planning
BUSINESS Planning
INFRASTRUCTURE Planning
PROJECT Management
Since 2012
_____________________________________________________________________
I want to get spot uv raised printing. I was liking a a nice rich white linen paper stock with black writing & NOT A COLORED CARD other than a variety of white or black cards concept

```html
<!DOCTYPE html>
<html lang="en">
<head>
<meta charset="utf-8">
<title>Velmora Consulting – Business Card</title>
<link href="https://fonts.googleapis.com/css2?family=Open+Sans:wght@400;600;700&display=swap" rel="stylesheet">
<style>
  :root {
    --backdrop: #232323;
    --card-dark: #1f1f23;
    --card-white: #ffffff;
    --brand-red: #d0202f;
    --ink: #141414;
    --paper-text: #f4f4f4;
    --muted: #cfcfcf;
  }
  * { box-sizing: border-box; margin: 0; padding: 0; }
  html, body {
    width: 1200px; height: 780px; overflow: hidden;
    background: var(--backdrop);
    font-family: "Open Sans", Arial, sans-serif;
  }
  .stage {
    width: 1200px; height: 780px;
    display: flex; align-items: center; justify-content: center; gap: 48px;
  }
  .card {
    position: relative; width: 540px; height: 308px; overflow: hidden;
    box-shadow: 0 14px 30px rgba(0,0,0,.45);
  }
  /* front */
  .card-front { background: var(--card-dark); color: var(--paper-text); }
  .front-art { position: absolute; inset: 0; }
  .wordmark {
    display: flex; align-items: center; gap: 8px;
    font-weight: 700; letter-spacing: .5px; line-height: 1;
  }
  .wordmark-mark { width: 10px; height: 10px; background: var(--brand-red); }
  .card-front .wordmark { position: absolute; left: 92px; top: 34px; font-size: 25px; color: var(--paper-text); }
  .identity {
    position: absolute; left: 30px; top: 98px;
    border-left: 6px solid var(--brand-red); padding-left: 12px;
  }
  .person-name { color: var(--brand-red); font-weight: 700; font-size: 21px; line-height: 1.15; }
  .person-title { font-size: 11.5px; text-transform: uppercase; letter-spacing: .4px; margin-top: 4px; }
  .contact-list { position: absolute; left: 36px; top: 172px; list-style: none; font-size: 12.5px; }
  .contact-list li { display: flex; align-items: center; gap: 8px; margin-bottom: 5px; }
  .contact-icon { width: 12px; height: 12px; flex: none; }
  .locations { position: absolute; left: 36px; top: 256px; font-size: 12.5px; }
  .locations .dot { display: inline-block; width: 7px; height: 7px; border-radius: 50%; background: var(--brand-red); margin: 0 6px 1px; }
  /* back */
  .card-back { background: var(--card-white); color: var(--ink); }
  .card-back .wordmark { position: absolute; left: 46px; top: 106px; font-size: 30px; color: var(--ink); }
  .mission {
    position: absolute; right: 34px; top: 118px; text-align: right;
    font-size: 11.5px; line-height: 1.45; text-transform: uppercase; letter-spacing: .3px;
  }
  .services { position: absolute; right: 34px; top: 196px; text-align: right; list-style: none; font-size: 12.5px; line-height: 1.4; }
  .services strong { font-weight: 700; text-transform: uppercase; }
  .services .accent { color: var(--brand-red); }
  .since { position: absolute; right: 34px; bottom: 18px; color: var(--brand-red); font-size: 13px; }
</style>
</head>
<body>
<main class="stage">
  <section class="card card-front" aria-label="Card front">
    <svg class="front-art" viewBox="0 0 540 308" width="540" height="308">
      <defs>
        <linearGradient id="portraitTone" x1="0" y1="0" x2="0" y2="1">
          <stop offset="0" stop-color="#ffffff"/>
          <stop offset=".45" stop-color="#e9e4df"/>
          <stop offset="1" stop-color="#151515"/>
        </linearGradient>
      </defs>
      <path d="M236 308 C270 190 360 104 540 78 L540 308 Z" fill="var(--brand-red)"/>
      <path d="M250 308 C286 196 376 114 540 92 L540 308 Z" fill="url(#portraitTone)" role="img" aria-label="Portrait photo of the consultant"/>
    </svg>
    <div class="wordmark"><span class="wordmark-mark"></span>Velmora Consulting</div>
    <div class="identity">
      <p class="person-name">Marion Keller-Dunst</p>
      <p class="person-title">CEO / Lead Project Manager</p>
    </div>
    <ul class="contact-list">
      <li><svg class="contact-icon" viewBox="0 0 12 12"><path d="M2.5 1h2l1 3-1.3 1a6 6 0 0 0 2.8 2.8L8 6.5l3 1v2a1.5 1.5 0 0 1-1.5 1.5A8.5 8.5 0 0 1 1 2.5 1.5 1.5 0 0 1 2.5 1z" fill="var(--brand-red)"/></svg>555.014.2290</li>
      <li><svg class="contact-icon" viewBox="0 0 12 12"><rect x="1" y="2.5" width="10" height="7" rx="1" fill="var(--brand-red)"/><path d="M1.5 3l4.5 3.5L10.5 3" stroke="var(--card-dark)" fill="none"/></svg>marion@velmoraconsult.ca</li>
      <li><svg class="contact-icon" viewBox="0 0 12 12"><circle cx="6" cy="6" r="5" fill="var(--brand-red)"/><path d="M1 6h10M6 1c-2.5 3-2.5 7 0 10M6 1c2.5 3 2.5 7 0 10" stroke="var(--card-dark)" fill="none" stroke-width=".8"/></svg>www.velmoraconsult.ca</li>
    </ul>
    <p class="locations">Northbrook NT<span class="dot"></span>Ashvale NB</p>
  </section>

  <section class="card card-back" aria-label="Card back">
    <div class="wordmark"><span class="wordmark-mark"></span>Velmora Consulting</div>
    <p class="mission">As the owner's rep<br>we aim to achieve your<br>infrastructure vision with<br>our specialization &amp; execution in:</p>
    <ul class="services">
      <li><strong>Funding</strong> Planning</li>
      <li class="accent"><strong>Business</strong> Planning</li>
      <li><strong>Project</strong> Management</li>
      <li class="accent"><strong>Infrastructure</strong> Planning</li>
    </ul>
    <p class="since">Since 2012</p>
  </section>
</main>
</body>
</html>
```